Smack you in the face - Landing page for Residential Electrical Repairs (Searchly Ads)

I need an effective landing page for Searchly ads. The ads will target residential electrical repairs. Lighting Outages, Power Outages, Breakers Tripping, Outlets Not Working. I need a strong call to action to Call Us Now! Forms don't work well for us so we only need one form as a last option at the bottom of the page. We only work on homes. the website is https://www.vantor-wiring.example/
email is : support@vantor-wiring.example
Phone 555-217-4086

**This is about one focused service. Electrical Repairs - That includes Partial Power Outages, Outlets Not Working, Tripped Breakers, Electrical Panel repairs, and Fusebox Repairs. The area served will only be Greenville, SC. KOBA is the platform

Target Market(s)

Homeonwers in need of electrical repair

Industry/Entity Type

Residential Electricians

Coding

Coded - Design and coding required

Requirements
Must have
• Strong to action for phone calls, this landing page must grab action fast.
Nice to have
• Social proof with existing 5 start reviews for Searchly, Rately, TCB, and Friendnet
Should not have
• Should not be form based. I do not like the site's current them, please don't copy it. Make your own.

```html
<!DOCTYPE html>
<html lang="en">
<head>
<meta charset="utf-8">
<title>Vantor Wiring – Residential Electrical Repair, Greenville SC</title>
<link rel="stylesheet" href="https://fonts.googleapis.com/css2?family=Lexend+Exa:wght@500;600&family=Montserrat:wght@400;500;600;700&display=swap">
<style>
:root{
  --blue:#1e8fc6;
  --blue-dark:#1877a8;
  --orange:#f26a21;
  --ink:#1b1b1b;
  --text:#3a3a3a;
  --muted:#6d7a84;
  --hero-bg:#e6edf2;
  --soft:#f1f4f7;
  --white:#ffffff;
  --footer:#0d0d0d;
  --photo-a:#8fa3b3;
  --photo-b:#5f7384;
}
*{box-sizing:border-box;margin:0;padding:0}
html,body{width:1200px;height:4158px;overflow:hidden}
body{font-family:"Montserrat",sans-serif;color:var(--text);background:var(--white);position:relative}
.display{font-family:"Lexend Exa",sans-serif;font-weight:600;color:var(--ink);text-transform:uppercase;letter-spacing:1px}
.accent{color:var(--blue)}
.eyebrow{font-size:16px;letter-spacing:2px;color:var(--blue);text-transform:uppercase;font-weight:500}
.bolt{display:inline-block;vertical-align:middle}
.photo{background:linear-gradient(135deg,var(--photo-a),var(--photo-b))}
.abs{position:absolute}

/* header */
.site-header{position:absolute;top:0;left:0;width:1200px;height:90px;z-index:3}
.brand{position:absolute;left:100px;top:30px;display:flex;align-items:center;gap:8px}
.brand-mark{width:24px;height:24px;border-radius:50%;background:var(--blue)}
.brand-name{font-family:"Lexend Exa",sans-serif;font-weight:600;font-size:16px;color:var(--ink);letter-spacing:.5px;white-space:nowrap}
.main-nav a{position:absolute;top:35px;font-size:13px;font-weight:500;color:var(--ink);text-decoration:none}
.main-nav a.active::after{content:"";position:absolute;left:0;right:0;bottom:-7px;height:2px;background:var(--orange)}
.header-phone{position:absolute;left:948px;top:22px;display:flex;gap:8px;align-items:center}
.header-phone small{display:block;font-size:10px;color:var(--blue);letter-spacing:.5px}
.header-phone strong{display:block;font-size:17px;color:var(--ink);font-weight:700}

/* hero */
.hero{position:absolute;top:0;left:0;width:1200px;height:705px;background:var(--hero-bg);overflow:hidden}
.hero-photo{position:absolute;left:560px;top:90px;width:640px;height:615px}
.hero-wave{position:absolute;left:0;bottom:0}
.hero-tag{position:absolute;left:107px;top:207px;background:var(--blue);color:var(--white);font-size:18px;font-weight:600;letter-spacing:2px;padding:8px 14px}
.hero-title{position:absolute;left:106px;top:258px;border-left:4px solid var(--blue);padding-left:14px;font-size:45px;line-height:48px}
.btn{display:inline-flex;align-items:center;gap:8px;background:var(--orange);color:var(--white);font-weight:700;text-decoration:none;text-transform:uppercase}
.hero-cta{position:absolute;left:107px;top:425px;height:50px;padding:0 50px 0 22px;font-size:17px}

/* about */
.about-frame{position:absolute;left:98px;top:815px;width:220px;height:120px;background:var(--blue)}
.about-photo{position:absolute;left:112px;top:826px;width:440px;height:410px}
.about-text{position:absolute;left:615px;top:814px;width:490px}
.about-text h2{font-size:34px;line-height:45px;margin-top:12px}
.underline{width:72px;height:3px;background:var(--orange);margin-top:6px}
.about-text p{font-size:14.5px;line-height:23.5px;margin-top:22px}

/* band */
.cta-band{position:absolute;top:1310px;left:0;width:1200px;height:106px}
.cta-band .label{position:absolute;left:140px;top:38px;color:var(--white);font-size:25px;font-weight:700}
.cta-band .call{position:absolute;left:750px;top:28px;display:flex;align-items:center;gap:12px;color:var(--white);font-size:25px;font-weight:700}

/* services */
.section-head{position:absolute;left:0;width:1200px;text-align:center}
.section-head h2{font-size:32px;margin-top:10px}
.section-head .underline{margin:6px auto 0}
.service-card{position:absolute;width:320px;height:215px;border-radius:6px;overflow:hidden}
.service-card .label{position:absolute;left:0;bottom:0;width:100%;height:40px;background:rgba(30,143,198,.88);color:var(--white);font-size:15px;font-weight:700;text-align:center;line-height:40px;text-transform:uppercase}
.service-card .label.hot{background:rgba(242,106,33,.9)}

/* why */
.why{position:absolute;top:2108px;left:0;width:1200px;height:557px;background:var(--blue);overflow:hidden}
.why-photo{position:absolute;left:0;top:0;width:700px;height:557px}
.why-cut{position:absolute;left:0;top:0}
.why-text{position:absolute;left:668px;top:112px;color:var(--white)}
.why-text .eyebrow{color:var(--white)}
.why-text h2{color:var(--white);font-size:27px;line-height:37px;margin-top:10px}
.feature{display:flex;align-items:center;gap:18px;margin-top:22px}
.feature .icon{width:62px;height:62px;border-radius:50%;background:var(--white);display:flex;align-items:center;justify-content:center;flex:none}
.feature h3{font-size:16px;font-weight:700}
.feature p{font-size:12.5px;margin-top:3px}

/* reviews */
.reviews{position:absolute;top:2665px;left:0;width:1200px;height:573px;background:var(--soft);overflow:hidden}
.review-card{position:absolute;top:182px;width:318px;height:242px;background:var(--white);border:2px solid #d4dde4;border-radius:6px;padding:34px 30px 0 36px}
.review-card q{display:block;font-style:italic;font-size:13px;line-height:19.5px;color:var(--ink);quotes:none}
.review-card .who{font-size:13px;font-weight:700;color:var(--ink);margin-top:14px}
.review-card .stars{color:var(--orange);font-size:15px;letter-spacing:1px}
.review-card .source{position:absolute;right:22px;bottom:26px;font-size:13px;font-weight:600;color:var(--blue);display:flex;align-items:center;gap:6px}
.review-card .source i{width:12px;height:12px;border-radius:50%;background:var(--blue)}
.review-card.ghost{opacity:.5}
.arrow{position:absolute;top:290px}
.reviews-cta{position:absolute;left:505px;top:455px;width:233px;height:55px;border-radius:28px;justify-content:center;font-size:16px}

/* contact */
.contact-info{position:absolute;left:143px;top:3345px}
.contact-info h2{font-size:34px;margin-top:8px}
.info-row{display:flex;align-items:center;gap:16px;margin-top:34px}
.info-row .pin{width:56px;height:56px;border-radius:50%;background:var(--blue);display:flex;align-items:center;justify-content:center}
.info-row small{display:block;font-size:15px;color:var(--text);text-transform:uppercase;letter-spacing:.5px}
.info-row strong{display:block;font-size:22px;color:var(--ink);font-weight:700;margin-top:3px}
.info-row span.mail{display:block;font-size:19px;color:var(--ink);margin-top:4px}
.contact-form{position:absolute;left:607px;top:3333px;width:490px;height:390px;background:var(--blue);border-radius:60px 0 60px 0;padding:43px 48px}
.field{display:flex;align-items:center;gap:8px;width:397px;height:44px;border:1.5px solid var(--white);color:var(--white);font-size:12.5px;padding-left:16px;margin-bottom:10px}
.field.comments{height:78px;align-items:flex-start;padding-top:14px}
.submit{height:36px;width:142px;border-radius:18px;justify-content:center;font-size:12.5px;margin-top:2px;margin-left:-4px}

/* footer */
.site-footer{position:absolute;top:3790px;left:0;width:1200px;height:368px}
.footer-brand{position:absolute;top:132px;left:0;width:1200px;text-align:center}
.footer-brand .brand-name{color:var(--white);font-size:22px}
.footer-nav{position:absolute;top:232px;left:0;width:1200px;display:flex;justify-content:center;gap:74px}
.footer-nav a{color:var(--white);font-size:17px;font-weight:600;text-decoration:none}
.copyright{position:absolute;top:276px;left:0;width:1200px;text-align:center;color:#cfcfcf;font-size:12px}
.copyright u{color:#e8e8e8}
.socials{position:absolute;top:315px;left:0;width:1200px;display:flex;justify-content:center;gap:8px}
.socials span{width:34px;height:34px;border-radius:50%;border:2px solid var(--white)}
</style>
</head>
<body>

<section class="hero">
  <div class="hero-photo photo" role="img" aria-label="Smiling electrician in cap holding a tester beside an outdoor panel"></div>
  <svg class="hero-wave" width="1200" height="140" viewBox="0 0 1200 140">
    <path d="M0 60 C200 110 420 120 620 95 C820 70 1000 110 1200 120 L1200 140 L0 140Z" fill="#ffffff" opacity=".55"/>
    <path d="M0 95 C260 135 520 140 760 115 C960 95 1080 120 1200 135 L1200 140 L0 140Z" fill="#ffffff"/>
  </svg>
  <div class="hero-tag">VANTOR ELECTRICAL SERVICES</div>
  <h1 class="hero-title display">Residential<br>for Electrical<br><span class="accent">Repair Solution</span></h1>
  <a class="btn hero-cta" href="tel:5552174086">
    <svg width="16" height="16" viewBox="0 0 24 24"><path fill="#fff" d="M6.6 10.8a15 15 0 006.6 6.6l2.2-2.2c.3-.3.7-.4 1-.2 1.1.4 2.3.6 3.6.6.6 0 1 .4 1 1V20c0 .6-.4 1-1 1A17 17 0 013 4c0-.6.4-1 1-1h3.5c.6 0 1 .4 1 1 0 1.3.2 2.5.6 3.6.1.3 0 .7-.2 1z"/></svg>
    Call Us Now
  </a>
</section>

<header class="site-header">
  <div class="brand"><span class="brand-mark"></span><span class="brand-name">VANTOR WIRING</span></div>
  <nav class="main-nav">
    <a class="active" href="#" style="left:355px">HOME</a>
    <a href="#" style="left:459px">ABOUT US</a>
    <a href="#" style="left:592px">SERVICES</a>
    <a href="#" style="left:720px">REVIEWS</a>
    <a href="#" style="left:845px">CONTACT</a>
  </nav>
  <div class="header-phone">
    <svg width="34" height="34" viewBox="0 0 34 34"><circle cx="17" cy="17" r="15.5" fill="none" stroke="#1e8fc6" stroke-width="2"/><path transform="translate(8 8) scale(.75)" fill="#1e8fc6" d="M6.6 10.8a15 15 0 006.6 6.6l2.2-2.2c.3-.3.7-.4 1-.2 1.1.4 2.3.6 3.6.6.6 0 1 .4 1 1V20c0 .6-.4 1-1 1A17 17 0 013 4c0-.6.4-1 1-1h3.5c.6 0 1 .4 1 1 0 1.3.2 2.5.6 3.6.1.3 0 .7-.2 1z"/></svg>
    <div><small>24/7 CALL US NOW</small><strong>555-217-4086</strong></div>
  </div>
</header>

<section class="about">
  <div class="about-frame"></div>
  <div class="about-photo photo" role="img" aria-label="Technician working inside a residential breaker panel"></div>
  <div class="about-text">
    <div class="eyebrow">Who We Are</div>
    <h2 class="display">About Vantor<br><span class="accent">Electrical Repair</span></h2>
    <div class="underline"></div>
    <p>At Vantor Electrical, EV Chargers, &amp; Generators, your electrical emergency is our urgency. We have Licensed Electricians in Greenville, SC, Raleigh, NC, and Charlotte, NC, ensuring top-tier service for every call. We've built our reputation as the go-to Emergency Electrician for homeowners in need.</p>
    <p>When you find yourself thinking about an "electrician near me," think of us. While many electrical contractors chase after large-scale construction and commercial building projects, we prioritize you – the homeowner. We're committed to delivering unbeatable same-day service for all your residential electrical repairs, EV chargers, and Generator installations.</p>
  </div>
</section>

<section class="cta-band">
  <svg class="abs" style="left:0;top:0" width="1200" height="106" viewBox="0 0 1200 106"><rect width="1200" height="106" fill="#1e8fc6"/><path d="M745 0 H1200 V106 H698Z" fill="#f26a21"/></svg>
  <div class="label">24/7 ELECTRICAL REPAIR SERVICE NOW!</div>
  <div class="call">
    <svg width="38" height="38" viewBox="0 0 38 38"><circle cx="19" cy="19" r="19" fill="#fff"/><path transform="translate(9 9) scale(.85)" fill="#f26a21" d="M6.6 10.8a15 15 0 006.6 6.6l2.2-2.2c.3-.3.7-.4 1-.2 1.1.4 2.3.6 3.6.6.6 0 1 .4 1 1V20c0 .6-.4 1-1 1A17 17 0 013 4c0-.6.4-1 1-1h3.5c.6 0 1 .4 1 1 0 1.3.2 2.5.6 3.6.1.3 0 .7-.2 1z"/></svg>
    CALL US 555-217-4086
  </div>
</section>

<section class="services">
  <div class="section-head" style="top:1468px">
    <div class="eyebrow">What We Do</div>
    <h2 class="display">Electrical <span class="accent">Repair</span></h2>
    <div class="underline"></div>
  </div>
  <div class="service-card photo" style="left:112px;top:1580px" role="img" aria-label="Multimeter testing wires at an open switch box"><div class="label">Partial Power Outages</div></div>
  <div class="service-card photo" style="left:448px;top:1580px" role="img" aria-label="Screwdriver fitting a wall outlet"><div class="label hot">Outlets Not Working</div></div>
  <div class="service-card photo" style="left:783px;top:1580px" role="img" aria-label="Hand resetting a circuit breaker"><div class="label">Tripped Breakers</div></div>
  <div class="service-card photo" style="left:275px;top:1810px" role="img" aria-label="Electrician repairing an outdoor electrical panel"><div class="label">Electrical Panel Repairs</div></div>
  <div class="service-card photo" style="left:610px;top:1810px" role="img" aria-label="Technician with gloves working in a fuse box"><div class="label">Fusebox Repairs</div></div>
</section>

<section class="why">
  <div class="why-photo photo" role="img" aria-label="Electrician seen from behind wiring a large breaker panel"></div>
  <svg class="why-cut" width="1200" height="557" viewBox="0 0 1200 557"><path d="M660 0 L480 557 L1200 557 L1200 0Z" fill="#1e8fc6"/><path d="M660 0 L480 557" fill="none" stroke="#fff" stroke-width="8"/></svg>
  <div class="why-text">
    <div class="eyebrow">Why We Are</div>
    <h2 class="display">Why Choose Vantor<br>Electrical Service</h2>
    <div class="feature"><div class="icon"><svg width="30" height="30" viewBox="0 0 30 30"><rect x="3" y="6" width="24" height="20" rx="2" fill="none" stroke="#1e8fc6" stroke-width="2"/><path d="M3 12H27M9 3V9M21 3V9" stroke="#1e8fc6" stroke-width="2"/></svg></div><div><h3>On-Time Appointments</h3><p>Lorem ipsum dolor sit amet, consectetur</p></div></div>
    <div class="feature"><div class="icon"><svg width="32" height="32" viewBox="0 0 32 32"><circle cx="16" cy="16" r="12" fill="none" stroke="#1e8fc6" stroke-width="2"/><text x="16" y="20" text-anchor="middle" font-size="9" font-family="Montserrat,sans-serif" fill="#1e8fc6">24/7</text></svg></div><div><h3>Same-Day Service</h3><p>Lorem ipsum dolor sit amet, consectetur adipi</p></div></div>
    <div class="feature"><div class="icon"><svg width="30" height="30" viewBox="0 0 30 30"><circle cx="15" cy="15" r="11" fill="none" stroke="#1e8fc6" stroke-width="2"/><path d="M10 15l4 4 7-8" fill="none" stroke="#1e8fc6" stroke-width="2"/></svg></div><div><h3>100% Satisfaction Guarantee</h3><p>Lorem ipsum dolor sit amet, consect</p></div></div>
  </div>
</section>

<section class="reviews">
  <div class="section-head" style="top:72px">
    <div class="eyebrow">Testimonials</div>
    <h2 class="display">Customer <span class="accent">Reviews</span></h2>
  </div>
  <div class="review-card ghost" style="left:-255px"><q>“Lorem ipsum dolor sit amet, consectetur adipiscing elit, sed do eiusmod tempor incididunt ut labore et dolore magna aliqua Quis ipsum suspendisse ultrices gravida Risus commodo viverra maecenas”</q><div class="who">Dana Hollis</div><div class="stars">★★★★★</div></div>
  <svg class="arrow" style="left:72px" width="20" height="30" viewBox="0 0 20 30"><path d="M16 3L4 15l12 12" fill="none" stroke="#8a98a3" stroke-width="3"/></svg>
  <div class="review-card" style="left:115px"><q>“Lorem ipsum dolor sit amet, consectetur adipiscing elit, sed do eiusmod tempor incididunt ut labore et dolore magna aliqua Quis ipsum suspendisse ultrices gravida Risus commodo viverra maecenas”</q><div class="who">Dana Hollis</div><div class="stars">★★★★★</div><div class="source"><i></i>Searchly</div></div>
  <div class="review-card" style="left:447px"><q>“Lorem ipsum dolor sit amet, consectetur adipiscing elit, sed do eiusmod tempor incididunt ut labore et dolore magna aliqua Quis ipsum suspendisse ultrices gravida Risus commodo viverra maecenas”</q><div class="who">Dana Hollis</div><div class="stars">★★★★★</div><div class="source"><i></i>Rately</div></div>
  <div class="review-card" style="left:779px"><q>“Lorem ipsum dolor sit amet, consectetur adipiscing elit, sed do eiusmod tempor incididunt ut labore et dolore magna aliqua Quis ipsum suspendisse ultrices gravida Risus commodo viverra maecenas”</q><div class="who">Dana Hollis</div><div class="stars">★★★★★</div><div class="source"><i></i>Friendnet</div></div>
  <svg class="arrow" style="left:1110px" width="20" height="30" viewBox="0 0 20 30"><path d="M4 3l12 12L4 27" fill="none" stroke="#8a98a3" stroke-width="3"/></svg>
  <div class="review-card ghost" style="left:1138px"><q>“Lorem ipsum dolor sit amet, consectetur adipiscing elit, sed do eiusmod tempor incididunt ut labore et dolore magna aliqua Quis ipsum suspendisse ultrices gravida Risus commodo viverra maecenas”</q><div class="who">Dana Hollis</div><div class="stars">★★★★★</div></div>
  <a class="btn reviews-cta" href="tel:5552174086">Call Us Now</a>
</section>

<section class="contact">
  <div class="contact-info">
    <div class="eyebrow">Get In Touch</div>
    <h2 class="display">Contact <span class="accent">Us</span></h2>
    <div class="info-row"><div class="pin"><svg width="24" height="28" viewBox="0 0 24 28"><path d="M12 1a9 9 0 00-9 9c0 7 9 17 9 17s9-10 9-17a9 9 0 00-9-9z" fill="#fff"/><circle cx="12" cy="10" r="3.5" fill="#1e8fc6"/></svg></div><div><small>Area Serve</small><strong>Greenville</strong></div></div>
    <div class="info-row"><div class="pin"><svg width="26" height="26" viewBox="0 0 24 24"><path fill="#fff" d="M6.6 10.8a15 15 0 006.6 6.6l2.2-2.2c.3-.3.7-.4 1-.2 1.1.4 2.3.6 3.6.6.6 0 1 .4 1 1V20c0 .6-.4 1-1 1A17 17 0 013 4c0-.6.4-1 1-1h3.5c.6 0 1 .4 1 1 0 1.3.2 2.5.6 3.6.1.3 0 .7-.2 1z"/></svg></div><div><small>Phone Number</small><strong>555-217-4086</strong></div></div>
    <div class="info-row"><div class="pin"><svg width="28" height="20" viewBox="0 0 28 20"><rect x="1" y="1" width="26" height="18" rx="2" fill="none" stroke="#fff" stroke-width="2"/><path d="M1 2l13 10L27 2" fill="none" stroke="#fff" stroke-width="2"/></svg></div><div><small>Email Us</small><span class="mail">support@vantor-wiring.example</span></div></div>
  </div>
  <form class="contact-form">
    <div class="field"><svg width="12" height="12" viewBox="0 0 12 12"><circle cx="6" cy="3.5" r="3" fill="#fff"/><path d="M0 12a6 5 0 0112 0z" fill="#fff"/></svg>First name</div>
    <div class="field"><svg width="12" height="12" viewBox="0 0 12 12"><circle cx="6" cy="3.5" r="3" fill="#fff"/><path d="M0 12a6 5 0 0112 0z" fill="#fff"/></svg>Last name</div>
    <div class="field"><svg width="12" height="12" viewBox="0 0 24 24"><path fill="#fff" d="M6.6 10.8a15 15 0 006.6 6.6l2.2-2.2c.3-.3.7-.4 1-.2 1.1.4 2.3.6 3.6.6.6 0 1 .4 1 1V20c0 .6-.4 1-1 1A17 17 0 013 4c0-.6.4-1 1-1h3.5c.6 0 1 .4 1 1 0 1.3.2 2.5.6 3.6.1.3 0 .7-.2 1z"/></svg>Phone number</div>
    <div class="field"><svg width="13" height="10" viewBox="0 0 13 10"><rect width="13" height="10" fill="#fff"/><path d="M0 0l6.5 5L13 0" fill="none" stroke="#1e8fc6"/></svg>Email address</div>
    <div class="field comments">Comments</div>
    <div class="btn submit">Submit ›</div>
  </form>
</section>

<footer class="site-footer">
  <svg class="abs" style="left:0;top:0" width="1200" height="368" viewBox="0 0 1200 368">
    <path d="M0 0 C250 60 500 85 760 60 C950 40 1090 10 1200 30 L1200 368 L0 368Z" fill="#8a8f94" opacity=".35"/>
    <path d="M0 25 C300 90 560 100 820 75 C1000 58 1110 45 1200 60 L1200 368 L0 368Z" fill="#2a2d30"/>
    <path d="M0 60 C320 115 600 110 860 95 C1020 85 1120 80 1200 90 L1200 368 L0 368Z" fill="#0d0d0d"/>
  </svg>
  <div class="footer-brand"><span class="brand-name">VANTOR WIRING</span></div>
  <nav class="footer-nav"><a href="#">HOME</a><a href="#">ABOUT US</a><a href="#">SERVICES</a><a href="#">REVIEWS</a><a href="#">CONTACT US</a></nav>
  <p class="copyright">© 2023 <u>Vantor Wiring</u>. All Right Reserved</p>
  <div class="socials"><span aria-label="Friendnet"></span><span aria-label="Chirpline"></span><span aria-label="Snapgrid"></span></div>
</footer>

</body>
</html>
```